Dunmore Roofing

Want a professional looking business card

Industry/Entity Type

Business

Contact Information for Business Card

Paul Dunmore ( Owner) paul@dunmoreroofing-example.com, www.dunmoreroofing-example.com, Adress: 4172 Township road 43 Alderbrook,NB K9X4T2

```html
<!DOCTYPE html>
<html lang="en">
<head>
<meta charset="utf-8">
<title>Dunmore Roofing – Business Card</title>
<link href="https://fonts.googleapis.com/css2?family=Oswald:wght@500&family=Open+Sans:wght@400&display=swap" rel="stylesheet">
<style>
  :root {
    --backdrop: #dcdcdc;
    --card-dark-1: #141414;
    --card-dark-2: #2e2e2e;
    --mark-grey: #8c8c8c;
    --brand-blue: #1f4b8f;
    --text-grey: #8a8a8a;
    --rule-grey: #9a9a9a;
    --white: #ffffff;
  }
  * { margin: 0; padding: 0; box-sizing: border-box; }
  html, body { width: 1200px; height: 1000px; overflow: hidden; }
  body { background: var(--backdrop); position: relative; font-family: "Open Sans", sans-serif; }

  .card {
    position: absolute;
    left: 269px;
    width: 662px;
    height: 378px;
    box-shadow: 0 2px 6px rgba(0,0,0,.25);
  }
  .card--front {
    top: 108px;
    background: linear-gradient(120deg, var(--card-dark-1) 0%, var(--card-dark-2) 100%);
  }
  .front-wordmark {
    position: absolute; top: 160px; left: 0; width: 100%;
    text-align: center;
    font-family: "Oswald", sans-serif;
    font-weight: 500;
    font-size: 54px;
    line-height: 64px;
    letter-spacing: 4px;
    color: var(--mark-grey);
    text-transform: uppercase;
  }

  .card--back { top: 521px; background: var(--white); }
  .back-wordmark {
    position: absolute; top: 80px; left: 0; width: 100%;
    text-align: center;
    font-family: "Oswald", sans-serif;
    font-weight: 500;
    font-size: 44px;
    line-height: 56px;
    letter-spacing: 2px;
    color: var(--brand-blue);
    text-transform: uppercase;
  }

  .person { position: absolute; right: 351px; top: 230px; text-align: right; }
  .person-name {
    font-family: "Oswald", sans-serif; font-weight: 500;
    font-size: 31px; line-height: 1.1; color: var(--brand-blue);
    text-transform: uppercase;
  }
  .person-role { font-size: 14px; color: var(--text-grey); margin-top: 2px; }

  .divider { position: absolute; left: 328px; top: 236px; width: 1px; height: 50px; background: var(--rule-grey); }

  .contacts { position: absolute; left: 346px; top: 231px; list-style: none; }
  .contacts li {
    display: flex; align-items: center; gap: 5px;
    font-size: 14px; line-height: 19px; color: var(--text-grey);
  }
  .contacts svg { width: 11px; height: 11px; fill: var(--brand-blue); flex: none; }

  .address-band {
    position: absolute; left: 0; right: 0; top: 326px; height: 40px;
    border-top: 1px solid var(--brand-blue);
    border-bottom: 1px solid var(--brand-blue);
    padding: 4px 0;
  }
  .address-band p {
    height: 30px; background: var(--brand-blue); color: var(--white);
    font-size: 14px; line-height: 30px; text-align: center;
  }
</style>
</head>
<body>
  <section class="card card--front" aria-label="Card front">
    <div class="front-wordmark">Dunmore Roofing</div>
  </section>

  <section class="card card--back" aria-label="Card back">
    <div class="back-wordmark">Dunmore Roofing</div>

    <div class="person">
      <div class="person-name">Paul Dunmore</div>
      <div class="person-role">Owner</div>
    </div>

    <div class="divider"></div>

    <ul class="contacts">
      <li>
        <svg viewBox="0 0 12 12" aria-hidden="true"><path d="M3 0h6a1 1 0 0 1 1 1v10a1 1 0 0 1-1 1H3a1 1 0 0 1-1-1V1a1 1 0 0 1 1-1zm0 1.5v8h6v-8z"/></svg>
        (555) 010-0147
      </li>
      <li>
        <svg viewBox="0 0 12 12" aria-hidden="true"><path d="M0 2h12v1L6 7 0 3zM0 4.3l6 4 6-4V10H0z"/></svg>
        paul@dunmoreroofing-example.com
      </li>
      <li>
        <svg viewBox="0 0 12 12" aria-hidden="true"><path d="M6 0a6 6 0 1 0 0 12A6 6 0 0 0 6 0zm0 1c.6 0 1.4 1.2 1.7 3H4.3C4.6 2.2 5.4 1 6 1zM1.2 5h2.1a10 10 0 0 0 0 2H1.2a5 5 0 0 1 0-2zm3.1 0h3.4a9 9 0 0 1 0 2H4.3a9 9 0 0 1 0-2zm4.4 0h2.1a5 5 0 0 1 0 2H8.7a10 10 0 0 0 0-2zM4.3 8h3.4C7.4 9.8 6.6 11 6 11s-1.4-1.2-1.7-3z"/></svg>
        www.dunmoreroofing-example.com
      </li>
    </ul>

    <div class="address-band">
      <p>Address: 4172 Township road 43 Alderbrook, NB K9X4T2</p>
    </div>
  </section>
</body>
</html>
```